Velmora Cabinets Letter Head and Email Signature

Hi
I would love a design package for a letterhead, email signature, even update my business card if you like if you can come up with a great idea for my new high end cabinet shop. Velmora Cabinets brings timeless craftsmanship to modern interiors, specializing in high end, custom cabinetry designed for architects and interior designers.

Target Market(s)

high end, luxury market

Industry/Entity Type

cabinet making

Requirements
Must have
• my colours of logo as the theme

```html
<!DOCTYPE html>
<html lang="en">
<head>
<meta charset="utf-8">
<title>Velmora Cabinets – Stationery Set</title>
<link rel="stylesheet" href="https://fonts.googleapis.com/css2?family=Montserrat:wght@400;500;600&display=swap">
<style>
  :root {
    --green: #4a7c46;
    --green-soft: #5e8f58;
    --black: #000000;
    --white: #ffffff;
    --paper-mark: #f1f2f0;
    --dark-mark: #1a1a1a;
    --rule-grey: #d6d6d6;
    --label: #f4ede4;
    --board-a: #6b3a1c;
    --board-b: #b0703a;
    --board-c: #7a4322;
  }
  * { box-sizing: border-box; margin: 0; padding: 0; }
  html, body { width: 1131px; height: 1200px; overflow: hidden; }
  body {
    position: relative;
    font-family: "Montserrat", sans-serif;
    background: linear-gradient(90deg, var(--board-a) 0%, var(--board-b) 45%, var(--board-b) 60%, var(--board-c) 100%);
  }
  .section-label {
    position: absolute;
    color: var(--label);
    font-size: 17px;
    font-weight: 500;
    letter-spacing: 0.5px;
    white-space: nowrap;
  }
  .abs { position: absolute; }

  /* Wordmark stand-in */
  .wordmark { position: absolute; display: flex; align-items: center; gap: 8px; color: var(--green); font-weight: 500; }
  .wordmark .mark-square { border: 2px solid var(--green); }
  .wordmark .name { line-height: 1; }
  .wordmark .name span { display: block; }
  .wordmark .sub { letter-spacing: 0.3em; }

  /* Contact lists */
  .contacts { position: absolute; list-style: none; }
  .contacts li { position: absolute; left: 0; display: flex; align-items: center; white-space: nowrap; }
  .contacts svg { flex: none; }

  /* Letterhead */
  .letterhead { left: 44px; top: 57px; width: 637px; height: 823px; background: var(--white); }
  .letterhead .header { position: absolute; left: 0; top: 0; width: 100%; height: 97px; background: var(--black); }
  .letterhead .header-rule { position: absolute; left: 0; top: 98px; width: 100%; height: 2px; background: var(--green); }
  .letterhead .contacts { left: 471px; top: 0; color: var(--white); font-size: 9px; }
  .letterhead .contacts li { gap: 6px; }
  .letterhead .faint-name {
    position: absolute; left: 0; top: 390px; width: 100%; text-align: center;
    color: var(--paper-mark); font-size: 64px; font-weight: 500; line-height: 1.05;
  }
  .letterhead .footer-rule { position: absolute; left: 145px; top: 768px; width: 346px; height: 1px; background: linear-gradient(90deg, transparent, var(--rule-grey) 15%, var(--rule-grey) 85%, transparent); }
  .letterhead .tagline { position: absolute; left: 0; top: 783px; width: 100%; text-align: center; color: var(--green-soft); font-size: 16px; letter-spacing: 0.3px; }

  /* Business card */
  .card { width: 298px; height: 170px; background: var(--black); color: var(--white); }
  .card-front { left: 750px; top: 270px; }
  .card-back { left: 751px; top: 453px; }
  .card .contacts { left: 21px; top: 0; font-size: 8px; }
  .card .contacts li { gap: 6px; }
  .person-name { position: absolute; font-weight: 600; white-space: nowrap; }
  .person-role { position: absolute; white-space: nowrap; letter-spacing: 0.3px; }
  .green-rule { position: absolute; height: 2px; background: var(--green); }
  .card .tagline-small { position: absolute; left: 21px; top: 145px; font-size: 8px; }
  .card-back .tagline { position: absolute; left: 0; top: 108px; width: 100%; text-align: center; font-size: 11.5px; letter-spacing: 0.3px; }

  /* Email signatures */
  .sig-dark { left: 121px; top: 917px; width: 442px; height: 194px; background: var(--black); color: var(--white); overflow: hidden; }
  .sig-dark .contacts { left: 22px; top: 0; font-size: 8px; }
  .sig-dark .contacts li { gap: 6px; }
  .sig-dark .faint-name { position: absolute; left: 240px; top: 40px; color: var(--dark-mark); font-size: 40px; font-weight: 500; line-height: 1.05; }
  .sig-light { left: 596px; top: 916px; width: 414px; height: 193px; background: var(--white); color: #222; }
  .sig-light .contacts { left: 24px; top: 0; font-size: 8px; }
  .sig-light .contacts li { gap: 7px; }
  .sig-light .tagline-small { position: absolute; right: 12px; top: 26px; font-size: 8px; color: var(--green); }
</style>
</head>
<body>

<!-- Letterhead -->
<div class="section-label" style="left:61px; top:27px;">Letterhead</div>
<section class="abs letterhead">
  <div class="header">
    <div class="wordmark" style="left:16px; top:22px;">
      <div class="mark-square" style="width:40px; height:40px;"></div>
      <div class="name"><span style="font-size:31px;">Velmora</span><span class="sub" style="font-size:14px; margin-top:4px;">CABINETS</span></div>
    </div>
    <ul class="contacts">
      <li style="top:19px;"><svg width="13" height="10" viewBox="0 0 13 10"><rect x="0.5" y="0.5" width="12" height="9" fill="var(--green)"/><path d="M0.5 0.5 L6.5 5.5 L12.5 0.5" fill="none" stroke="#000" stroke-width="1"/></svg>info@velmoracabinets.com.au</li>
      <li style="top:41px;"><svg width="13" height="12" viewBox="0 0 13 12"><rect x="3.5" y="0.5" width="6" height="11" rx="1" fill="none" stroke="var(--white)" stroke-width="1"/><rect x="5" y="2" width="3" height="6" fill="var(--green)"/></svg>040 555 0142</li>
      <li style="top:63px;"><svg width="13" height="13" viewBox="0 0 13 13"><circle cx="6.5" cy="6.5" r="5.5" fill="none" stroke="var(--green)" stroke-width="1.5"/></svg>@velmora.cabinets</li>
    </ul>
  </div>
  <div class="header-rule"></div>
  <div class="faint-name" aria-hidden="true">Velmora<br>Cabinets</div>
  <div class="footer-rule"></div>
  <p class="tagline">Timeless Craft. Modern Interiors.</p>
</section>

<!-- Business card -->
<div class="section-label" style="left:920px; top:233px;">Business Card</div>
<section class="abs card card-front">
  <ul class="contacts">
    <li style="top:17px;"><svg width="12" height="9" viewBox="0 0 12 9"><rect x="0.5" y="0.5" width="11" height="8" fill="var(--green)"/><path d="M0.5 0.5 L6 5 L11.5 0.5" fill="none" stroke="#000" stroke-width="1"/></svg>info@velmoracabinets.com.au</li>
    <li style="top:37px;"><svg width="12" height="11" viewBox="0 0 12 11"><rect x="3.5" y="0.5" width="5" height="10" rx="1" fill="none" stroke="var(--white)" stroke-width="1"/><rect x="5" y="2" width="2" height="5" fill="var(--green)"/></svg>040 555 0142</li>
    <li style="top:58px;"><svg width="12" height="12" viewBox="0 0 12 12"><circle cx="6" cy="6" r="5" fill="none" stroke="var(--green)" stroke-width="1.4"/></svg>@velmora.cabinets</li>
  </ul>
  <div class="wordmark" style="left:218px; top:20px;">
    <div class="name"><span style="font-size:17px;">Velmora</span><span class="sub" style="font-size:8px; margin-top:3px;">CABINETS</span></div>
  </div>
  <div class="green-rule" style="left:0; top:109px; width:15px;"></div>
  <div class="green-rule" style="left:116px; top:109px; width:182px;"></div>
  <div class="person-name" style="left:21px; top:99px; font-size:10.5px;">Owen Talbrook</div>
  <div class="person-role" style="left:21px; top:115px; font-size:6.5px;">Director Craftsman</div>
  <p class="tagline-small">Timeless Craft. Modern Interiors.</p>
</section>
<section class="abs card card-back">
  <div class="wordmark" style="left:48px; top:40px;">
    <div class="mark-square" style="width:48px; height:48px;"></div>
    <div class="name"><span style="font-size:34px;">Velmora</span><span class="sub" style="font-size:15px; margin-top:5px;">CABINETS</span></div>
  </div>
  <p class="tagline">Timeless Craft. Modern Interiors.</p>
</section>

<!-- Email signature, option 1 -->
<section class="abs sig-dark">
  <div class="faint-name" aria-hidden="true">Velmora<br>Cabinets</div>
  <div class="person-name" style="left:22px; top:19px; font-size:10.5px;">Owen Talbrook</div>
  <div class="person-role" style="left:22px; top:34px; font-size:6.5px;">Director Craftsman</div>
  <ul class="contacts">
    <li style="top:61px;"><svg width="12" height="9" viewBox="0 0 12 9"><rect x="0.5" y="0.5" width="11" height="8" fill="var(--green)"/><path d="M0.5 0.5 L6 5 L11.5 0.5" fill="none" stroke="#000" stroke-width="1"/></svg>info@velmoracabinets.com.au</li>
    <li style="top:81px;"><svg width="12" height="11" viewBox="0 0 12 11"><rect x="3.5" y="0.5" width="5" height="10" rx="1" fill="none" stroke="var(--white)" stroke-width="1"/><rect x="5" y="2" width="2" height="5" fill="var(--green)"/></svg>040 555 0142</li>
    <li style="top:101px;"><svg width="12" height="12" viewBox="0 0 12 12"><circle cx="6" cy="6" r="5" fill="none" stroke="var(--green)" stroke-width="1.4"/></svg>@velmora.cabinets</li>
  </ul>
  <div class="wordmark" style="left:22px; top:134px;">
    <div class="mark-square" style="width:32px; height:32px;"></div>
    <div class="name"><span style="font-size:25px;">Velmora</span><span class="sub" style="font-size:11px; margin-top:3px;">CABINETS</span></div>
  </div>
</section>
<div class="section-label" style="left:312px; top:1124px; transform:translateX(-50%);">Email Signature - Option 1</div>

<!-- Email signature, option 2 -->
<section class="abs sig-light">
  <div class="person-name" style="left:24px; top:25px; font-size:10.5px; color:var(--green);">Owen Talbrook</div>
  <div class="person-role" style="left:24px; top:41px; font-size:6.5px;">Director Craftsman</div>
  <div class="green-rule" style="left:0; top:38px; width:18px; height:1.5px;"></div>
  <div class="green-rule" style="left:147px; top:38px; width:267px; height:1.5px;"></div>
  <p class="tagline-small">Timeless Craft. Modern Interiors.</p>
  <ul class="contacts">
    <li style="top:79px;"><svg width="12" height="12" viewBox="0 0 12 12"><circle cx="6" cy="6" r="5.3" fill="none" stroke="var(--green)" stroke-width="1"/><path d="M4 3.5 L5 3.2 L5.6 4.8 L5 5.3 Q5.6 6.6 6.8 7.1 L7.3 6.5 L8.8 7.1 L8.5 8.2 Q5 8.5 4 3.5 Z" fill="var(--green)"/></svg>040 555 0142</li>
    <li style="top:97px;"><svg width="12" height="9" viewBox="0 0 12 9"><rect x="0.5" y="0.5" width="11" height="8" fill="var(--green)"/><path d="M0.5 0.5 L6 5 L11.5 0.5" fill="none" stroke="#fff" stroke-width="1"/></svg>info@velmoracabinets.com.au</li>
    <li style="top:115px;"><svg width="12" height="12" viewBox="0 0 12 12"><circle cx="6" cy="6" r="5" fill="none" stroke="var(--green)" stroke-width="1.4"/></svg>@velmora.cabinets</li>
    <li style="top:155px;"><svg width="12" height="14" viewBox="0 0 12 14"><path d="M6 13.5 C2.5 9 1 7 1 5 A5 5 0 0 1 11 5 C11 7 9.5 9 6 13.5 Z" fill="var(--green)"/><circle cx="6" cy="5" r="1.8" fill="#fff"/></svg>445 Street Name, City Name Australia 20854</li>
  </ul>
  <div class="wordmark" style="left:293px; top:137px;">
    <div class="mark-square" style="width:28px; height:28px;"></div>
    <div class="name"><span style="font-size:19px;">Velmora</span><span class="sub" style="font-size:9px; margin-top:3px;">CABINETS</span></div>
  </div>
</section>
<div class="section-label" style="left:819px; top:1124px; transform:translateX(-50%);">Email Signature - Option 2</div>

</body>
</html>
```